Change of trading name, rebrand

existing website to be updated with new theme and logo. existing website is
www.harlowbrentmere.com.au
Industry/Entity Type
Construction
Coding
Coded - Design and coding required
Number of Pages Required
5+ page
Requirements
Must have
- be mobile phone friendly

```html
<!DOCTYPE html>
<html lang="en">
<head>
<meta charset="utf-8">
<meta name="viewport" content="width=device-width, initial-scale=1">
<title>HBR Plant Hire</title>
<link href="https://fonts.googleapis.com/css2?family=Michroma&family=Montserrat:wght@400;500;600;700&display=swap" rel="stylesheet">
<style>
:root{
  --navy:#28296e;
  --navy-dark:#1f2058;
  --ink:#222;
  --body:#3a3a3a;
  --grey:#ececec;
  --line:#c9c9c9;
  --white:#fff;
}
*{box-sizing:border-box;margin:0;padding:0}
html,body{width:1200px;height:4029px;overflow:hidden}
body{font-family:"Montserrat",sans-serif;color:var(--ink);background:var(--white);position:relative}
.abs{position:absolute}
.display{font-family:"Michroma",sans-serif;font-weight:400;color:var(--navy);letter-spacing:1px}
.btn{position:absolute;display:flex;align-items:center;justify-content:center;background:var(--navy);color:#fff;font-weight:600;font-size:18px;border-radius:28px;letter-spacing:.5px}
.brand{font-weight:700;color:var(--navy);font-size:40px;letter-spacing:2px;display:flex;align-items:center;gap:10px}
.brand i{width:18px;height:18px;background:var(--navy);display:block}
.photo{position:absolute;border:6px solid #fff;box-shadow:0 2px 10px rgba(0,0,0,.25)}
.icon-circle{position:absolute;border-radius:50%;display:flex;align-items:center;justify-content:center}
/* header */
.contact-label{font-size:16px;color:var(--ink);letter-spacing:.5px}
.contact-value{font-size:16px;color:var(--navy);font-weight:600}
.nav{left:0;top:104px;width:1200px;height:52px;background:var(--navy)}
.nav a{position:absolute;top:20px;color:#fff;font-size:12px;font-weight:500;text-decoration:none}
.search{left:860px;top:104px;width:340px;height:52px;background:#111;clip-path:polygon(28px 0,100% 0,100% 100%,0 100%)}
.search span{position:absolute;left:50px;top:19px;color:#888;font-size:11px}
/* hero */
.hero{left:0;top:156px;width:1200px;height:515px;background:linear-gradient(90deg,#3a3f8c 0%,#5c5fa0 35%,#8f9cbf 55%,#c9ccd6 100%)}
.hero-tag{left:52px;top:250px;color:#fff;font-size:20px;font-weight:500}
.hero-title{left:52px;top:305px;color:#fff;font-size:27px;line-height:53px;font-family:"Michroma",sans-serif}
/* about */
.about-text{left:637px;top:830px;width:460px;font-size:15.5px;line-height:38.5px;color:var(--body)}
/* stats */
.stats{left:0;top:1327px;width:1200px;height:482px;background:var(--grey)}
.stat{position:absolute;width:260px;text-align:center}
.stat b{display:block;font-size:25px;font-weight:500;margin-bottom:6px}
.stat span{font-size:16px;font-weight:500;line-height:28px}
/* equipment */
.equip-label{position:absolute;width:150px;text-align:center;top:2034px;font-size:16px;font-weight:500}
.dump-text{left:111px;top:2206px;width:460px;font-size:15.5px;line-height:38.5px;color:var(--body)}
/* contact */
.contact{left:0;top:2693px;width:1200px;height:742px;background:var(--grey)}
.field{position:absolute;left:600px;width:488px;border:1px solid #888;border-radius:6px}
.field label{position:absolute;left:26px;top:-11px;background:var(--grey);padding:0 8px;font-size:15px;font-weight:600}
/* footer */
.foot-link{position:absolute;font-size:14.5px;font-weight:500;color:var(--ink)}
.rule{position:absolute;left:111px;width:977px;height:1px;background:var(--line)}
</style>
</head>
<body>

<!-- header -->
<div class="abs brand" style="left:112px;top:30px;font-size:40px"><i></i>HBR</div>
<svg class="abs" style="left:497px;top:26px" width="24" height="24" viewBox="0 0 24 24"><circle cx="12" cy="12" r="12" fill="var(--navy)"/><path d="M8 6.5c.6-.4 1.3 0 1.6.6l.8 1.7c.2.5 0 1-.4 1.3l-.7.5c.6 1.4 1.6 2.4 3 3l.5-.7c.3-.4.8-.6 1.3-.4l1.7.8c.6.3 1 1 .6 1.6-.7 1.2-2 1.7-3.2 1.2-2.8-1.1-4.8-3.1-5.9-5.9C6.8 8.6 7 7.2 8 6.5z" fill="#fff"/></svg>
<div class="abs contact-label" style="left:541px;top:26px">CALL US NOW</div>
<div class="abs contact-value" style="left:541px;top:62px">1300 482 915</div>
<svg class="abs" style="left:742px;top:26px" width="22" height="24" viewBox="0 0 22 24"><circle cx="11" cy="12" r="11" fill="var(--navy)"/><path d="M11 5a4.5 4.5 0 0 0-4.5 4.5c0 3.3 4.5 8.5 4.5 8.5s4.5-5.2 4.5-8.5A4.5 4.5 0 0 0 11 5z" fill="#fff"/><circle cx="11" cy="9.5" r="1.8" fill="var(--navy)"/></svg>
<div class="abs contact-label" style="left:780px;top:26px">REACH US NOW</div>
<div class="abs contact-value" style="left:780px;top:62px">18 WATTLEBANK RD, COOMERA QLD 4209</div>

<nav class="abs nav">
  <a style="left:70px;border-bottom:1px solid #fff;padding-bottom:2px">HOME</a>
  <a style="left:142px">ABOUT US</a>
  <a style="left:239px">PLANT HIRE</a>
  <a style="left:346px">MAJOR PROJECT SNAPSHOT</a>
  <a style="left:556px">POLICIES</a>
  <a style="left:649px">JOBS</a>
  <a style="left:714px">CONTACT US</a>
</nav>
<div class="abs search"><span>SEARCH HERE....</span>
  <svg class="abs" style="left:292px;top:19px" width="13" height="13" viewBox="0 0 13 13"><circle cx="5.5" cy="5.5" r="4" stroke="#fff" stroke-width="1.8" fill="none"/><path d="M8.5 8.5l3.5 3.5" stroke="#fff" stroke-width="1.8"/></svg>
</div>

<!-- hero -->
<div class="abs hero" role="img" aria-label="Yellow excavator on a dirt mound under a cloudy sky, tinted navy on the left"></div>
<div class="abs hero-tag">HBR HEAVY EQUIPMENT HIRE</div>
<div class="abs hero-title">COMMITTED TO SUPERIOR<br>QUALITY PLANT HIRE<br>SERVICES.</div>
<div class="btn" style="left:54px;top:497px;width:230px;height:58px;background:var(--navy-dark)">GET STARTED</div>

<!-- about -->
<div class="photo" role="img" aria-label="Excavator bucket lifting rubble on a demolition site" style="left:111px;top:766px;width:460px;height:462px;background:linear-gradient(160deg,#c9ccd2,#7d7e80 60%,#9a8c7a)"></div>
<h2 class="abs display" style="left:637px;top:762px;font-size:34px">ABOUT US</h2>
<p class="abs about-text">Harlow Brentmere Resources Pty Ltd trading as HBR Heavy Equipment is a privately owned company that was established in 2010. Our founder saw a need in the market for a plant and equipment supplier who was committed to the successful delivery of client's projects. With this vision and focus HBR has successfully seen our clients deliver on-time and on- budget. Taking the time to understand our clients requirements</p>
<div class="btn" style="left:637px;top:1167px;width:210px;height:55px">LEARN MORE</div>

<!-- stats -->
<div class="abs stats"></div>
<svg class="abs" style="left:16px;top:1553px" width="44" height="30" viewBox="0 0 44 30"><circle cx="28" cy="15" r="12" stroke="#222" stroke-width="1.6" fill="none"/><path d="M2 15h22M8 10l-6 5 6 5" stroke="#222" stroke-width="1.6" fill="none"/></svg>
<svg class="abs" style="left:1130px;top:1553px" width="44" height="30" viewBox="0 0 44 30"><circle cx="16" cy="15" r="12" stroke="var(--navy)" stroke-width="1.6" fill="none"/><path d="M20 15h22M36 10l6 5-6 5" stroke="var(--navy)" stroke-width="1.6" fill="none"/></svg>

<div class="icon-circle" role="img" aria-label="Worker in hi-vis vest on site" style="left:112px;top:1410px;width:215px;height:215px;border:3px solid var(--navy);background:linear-gradient(160deg,#d8d4c6,#8a8a6a)"></div>
<div class="icon-circle" role="img" aria-label="Orange excavator in a quarry" style="left:365px;top:1410px;width:215px;height:215px;border:3px solid var(--navy);background:linear-gradient(160deg,#b7c6d8,#7a6e64)"></div>
<div class="icon-circle" role="img" aria-label="Excavator loading a dump truck" style="left:619px;top:1410px;width:215px;height:215px;border:3px solid var(--navy);background:linear-gradient(160deg,#7fb0e0,#c9b070)"></div>
<div class="icon-circle" role="img" aria-label="Excavator on a demolition pile" style="left:872px;top:1410px;width:215px;height:215px;border:3px solid var(--navy);background:linear-gradient(160deg,#bcc2c8,#6a5e52)"></div>
<div class="icon-circle" style="left:180px;top:1570px;width:60px;height:60px;background:var(--navy);border:3px solid #fff"><svg width="28" height="20"><circle cx="14" cy="6" r="4" fill="#fff"/><path d="M6 19c0-5 4-7 8-7s8 2 8 7z" fill="#fff"/></svg></div>
<div class="icon-circle" style="left:443px;top:1570px;width:60px;height:60px;background:var(--navy);border:3px solid #fff"><svg width="28" height="20"><rect x="3" y="12" width="16" height="6" fill="#fff"/><path d="M10 12l8-9 7 5" stroke="#fff" stroke-width="2" fill="none"/></svg></div>
<div class="icon-circle" style="left:696px;top:1570px;width:60px;height:60px;background:var(--navy);border:3px solid #fff"><svg width="28" height="20"><rect x="2" y="9" width="18" height="7" fill="#fff"/><circle cx="6" cy="17" r="2" fill="#fff"/><circle cx="17" cy="17" r="2" fill="#fff"/><path d="M14 9l7-7 5 4" stroke="#fff" stroke-width="2" fill="none"/></svg></div>
<div class="icon-circle" style="left:950px;top:1570px;width:60px;height:60px;background:var(--navy);border:3px solid #fff"><svg width="28" height="20"><circle cx="8" cy="4" r="3" fill="#fff"/><rect x="5" y="8" width="6" height="11" fill="#fff"/><rect x="15" y="8" width="10" height="11" fill="#fff"/></svg></div>

<div class="stat" style="left:90px;top:1651px"><b>20+</b><span>YEARS OF EXPERIENCE</span></div>
<div class="stat" style="left:343px;top:1651px"><b>100+</b><span>MACHINES IN FLEET</span></div>
<div class="stat" style="left:597px;top:1651px"><b>60+</b><span>ONE OF QLD'S LARGEST<br>SUPPLIERS</span></div>
<div class="stat" style="left:850px;top:1651px"><b>45+</b><span>ONSITE SERVICING</span></div>

<!-- equipment -->
<svg class="abs" style="left:36px;top:1944px" width="30" height="16"><path d="M1 8h28M8 2L1 8l7 6" stroke="#222" stroke-width="2" fill="none"/></svg>
<svg class="abs" style="left:1122px;top:1944px" width="30" height="16"><path d="M1 8h28M22 2l7 6-7 6" stroke="#222" stroke-width="2" fill="none"/></svg>
<div class="icon-circle" style="left:109px;top:1903px;width:102px;height:102px;background:var(--navy);border:4px solid #b9bad6"><svg width="44" height="34"><rect x="4" y="20" width="24" height="10" fill="#fff"/><path d="M18 20l12-14 10 8" stroke="#fff" stroke-width="3" fill="none"/></svg></div>
<div class="icon-circle" style="left:254px;top:1903px;width:102px;height:102px;background:var(--navy);border:4px solid #b9bad6"><svg width="44" height="34"><rect x="8" y="8" width="20" height="14" fill="#fff"/><circle cx="12" cy="26" r="5" fill="#fff"/><circle cx="26" cy="26" r="5" fill="#fff"/><rect x="33" y="14" width="6" height="14" fill="#fff"/></svg></div>
<div class="icon-circle" style="left:400px;top:1903px;width:102px;height:102px;background:var(--navy);border:4px solid #b9bad6"><svg width="44" height="34"><rect x="6" y="10" width="16" height="10" fill="#fff"/><circle cx="8" cy="25" r="4" fill="#fff"/><circle cx="20" cy="25" r="4" fill="#fff"/><circle cx="36" cy="25" r="4" fill="#fff"/><path d="M22 16h16" stroke="#fff" stroke-width="3"/></svg></div>
<div class="icon-circle" style="left:547px;top:1903px;width:102px;height:102px;background:#fff;border:4px solid #b9bad6"><svg width="44" height="34"><rect x="2" y="8" width="28" height="14" fill="var(--navy)"/><rect x="31" y="12" width="10" height="10" fill="var(--navy)"/><circle cx="10" cy="26" r="4" fill="var(--navy)"/><circle cx="34" cy="26" r="4" fill="var(--navy)"/></svg></div>
<div class="icon-circle" style="left:692px;top:1903px;width:102px;height:102px;background:var(--navy);border:4px solid #b9bad6"><svg width="44" height="34"><rect x="8" y="8" width="16" height="14" fill="#fff"/><circle cx="12" cy="26" r="5" fill="#fff"/><circle cx="28" cy="26" r="5" fill="#fff"/><path d="M24 14l10 4 4 10" stroke="#fff" stroke-width="3" fill="none"/></svg></div>
<div class="icon-circle" style="left:838px;top:1903px;width:102px;height:102px;background:var(--navy);border:4px solid #b9bad6"><svg width="44" height="34"><rect x="8" y="6" width="28" height="10" fill="#fff"/><rect x="8" y="18" width="28" height="6" fill="#fff"/><circle cx="12" cy="28" r="4" fill="#fff"/><circle cx="32" cy="28" r="4" fill="#fff"/></svg></div>
<div class="icon-circle" style="left:984px;top:1903px;width:102px;height:102px;background:var(--navy);border:4px solid #b9bad6"><svg width="44" height="34"><rect x="14" y="6" width="14" height="12" fill="#fff"/><circle cx="10" cy="24" r="7" fill="#fff"/><circle cx="34" cy="26" r="5" fill="#fff"/></svg></div>
<div class="equip-label" style="left:85px">EXCAVATORS</div>
<div class="equip-label" style="left:230px">DOZERS</div>
<div class="equip-label" style="left:376px">GRADERS</div>
<div class="equip-label" style="left:523px;color:var(--navy)">DUMP TRUCKS</div>
<div class="equip-label" style="left:668px">LOADERS</div>
<div class="equip-label" style="left:814px">WATER CARTS</div>
<div class="equip-label" style="left:960px">COMPACTORS</div>

<h2 class="abs display" style="left:109px;top:2140px;font-size:32px">DUMP TRUCKS</h2>
<p class="abs dump-text">We are South East Queensland's material cartage and haulage specialists, with a range of road registered, track mounted and articulated dump trucks to suit your project requirements. We prefer late model Ardent, Veltro and Kimura Dump trucks, ranging from 25 tonne to 40 tonnes in capacity, and with and without tail gate options. HBR Heavy Equipment is proud of our new and well-maintained fleet</p>
<div class="btn" style="left:111px;top:2542px;width:211px;height:55px">LEARN MORE</div>
<div class="photo" role="img" aria-label="Large yellow mining dump truck in a gravel pit" style="left:622px;top:2140px;width:460px;height:462px;background:linear-gradient(180deg,#8a8478 0%,#9c958a 35%,#e89a2a 55%,#3a3a38 85%)"></div>

<!-- contact -->
<div class="abs contact"></div>
<h2 class="abs display" style="left:0;width:1200px;text-align:center;top:2743px;font-size:34px">CONTACT US</h2>
<svg class="abs" style="left:203px;top:2822px" width="30" height="30" viewBox="0 0 24 24"><circle cx="12" cy="12" r="12" fill="var(--navy)"/><path d="M8 6.5c.6-.4 1.3 0 1.6.6l.8 1.7c.2.5 0 1-.4 1.3l-.7.5c.6 1.4 1.6 2.4 3 3l.5-.7c.3-.4.8-.6 1.3-.4l1.7.8c.6.3 1 1 .6 1.6-.7 1.2-2 1.7-3.2 1.2-2.8-1.1-4.8-3.1-5.9-5.9C6.8 8.6 7 7.2 8 6.5z" fill="#fff"/></svg>
<div class="abs" style="left:257px;top:2828px;font-size:16px;font-weight:600">CALL US : 1300 482 915</div>
<svg class="abs" style="left:561px;top:2822px" width="28" height="30" viewBox="0 0 22 24"><circle cx="11" cy="12" r="11" fill="var(--navy)"/><path d="M11 5a4.5 4.5 0 0 0-4.5 4.5c0 3.3 4.5 8.5 4.5 8.5s4.5-5.2 4.5-8.5A4.5 4.5 0 0 0 11 5z" fill="#fff"/><circle cx="11" cy="9.5" r="1.8" fill="var(--navy)"/></svg>
<div class="abs" style="left:609px;top:2828px;font-size:16px;font-weight:600">REACH US : 18 WATTLEBANK RD, COOMERA QLD 4209</div>
<div class="photo" role="img" aria-label="Street map showing the depot location" style="left:112px;top:2906px;width:462px;height:466px;background:linear-gradient(135deg,#e9ecef 0%,#e3ead8 55%,#cfe8d4 100%)"></div>
<div class="field" style="top:2935px;height:58px"><label>FULL NAME</label></div>
<div class="field" style="top:3027px;height:58px"><label>EMAIL ADDRESS</label></div>
<div class="field" style="top:3115px;height:58px"><label>PHONE NUMBER</label></div>
<div class="field" style="top:3206px;height:82px"><label>ENQUIRY</label></div>
<div class="btn" style="left:600px;top:3315px;width:210px;height:55px">SUBMIT NOW</div>

<!-- partners -->
<svg class="abs" style="left:36px;top:3559px" width="30" height="16"><path d="M1 8h28M8 2L1 8l7 6" stroke="#222" stroke-width="2" fill="none"/></svg>
<svg class="abs" style="left:1122px;top:3559px" width="30" height="16"><path d="M1 8h28M22 2l7 6-7 6" stroke="#222" stroke-width="2" fill="none"/></svg>
<div class="abs" style="left:113px;top:3548px;width:120px;height:36px;background:#d5dae8;border-radius:4px"></div>
<div class="abs" style="left:284px;top:3548px;width:116px;height:36px;background:#d5dae8;border-radius:4px"></div>
<div class="abs" style="left:455px;top:3548px;width:116px;height:36px;background:#d5dae8;border-radius:4px"></div>
<div class="abs" style="left:628px;top:3548px;width:110px;height:36px;background:#d5dae8;border-radius:4px"></div>
<div class="abs" style="left:810px;top:3534px;width:90px;height:64px;background:#d5dae8;border-radius:4px"></div>
<div class="abs" style="left:968px;top:3548px;width:116px;height:36px;background:#d5dae8;border-radius:4px"></div>

<!-- footer -->
<div class="rule" style="top:3646px"></div>
<div class="abs brand" style="left:126px;top:3728px;font-size:36px"><i></i>HBR</div>
<div class="foot-link" style="left:346px;top:3698px">HOME</div>
<div class="foot-link" style="left:346px;top:3738px">ABOUT US</div>
<div class="foot-link" style="left:346px;top:3778px">MACHINE OPERATOR JOBS</div>
<div class="foot-link" style="left:346px;top:3818px">PLANT HIRE</div>
<div class="foot-link" style="left:346px;top:3858px">ATTACHMENTS HIRE</div>
<div class="foot-link" style="left:346px;top:3898px">POLICIES</div>
<div class="foot-link" style="left:612px;top:3698px">ARTICULATED DUMP TRUCKS HIRE</div>
<div class="foot-link" style="left:612px;top:3738px">DOZER HIRE</div>
<div class="foot-link" style="left:612px;top:3778px">EXCAVATOR DIGGERS HIRE</div>
<div class="foot-link" style="left:612px;top:3818px">GRADER HIRE</div>
<div class="foot-link" style="left:612px;top:3858px">ATTACHMENTS HIRE</div>
<div class="foot-link" style="left:931px;top:3698px">BACKHOE HIRE</div>
<div class="foot-link" style="left:931px;top:3738px">COMPACTORS HIRE</div>
<div class="foot-link" style="left:931px;top:3778px">LOADER HIRE</div>
<div class="foot-link" style="left:931px;top:3818px">SKID STEER HIRE</div>
<div class="foot-link" style="left:931px;top:3858px">WATER CART HIRE</div>
<div class="rule" style="top:3969px"></div>
<div class="abs" style="left:0;width:1200px;text-align:center;top:3988px;font-size:14px;color:var(--navy);font-weight:500">@2024 COPYRIGHTS - ALL RIGHTS RESERVED</div>

</body>
</html>
```